Shopify Web-Page "Tiny-ThreadDays

We are building a new business in Switzerland offering premium sewing holiday camps for kids aged 9–14. In enclosed brief outlines our requirements for a complete Shopify homepage design and a multilingual logo creation.
Domains: tiny-threaddays.ch ; tiny-giornifilo.ch ; tiny-fadentage.ch

Project Overview
We are looking for:
1. A modern, fully designed Shopify homepage in English using standard Shopify content blocks (no custom coding), which we can later update ourselves. Supporting Multilanguage (EN, German, Italian).

2. A logo design that includes the brand identity and communicates our multilingual, creative, and child-focused positioning.

All details in enclosed

```html
<!DOCTYPE html>
<html lang="en">
<head>
<meta charset="utf-8">
<title>Tiny-ThreadDays – Creative Sewing Camps for Kids</title>
<link rel="stylesheet" href="https://fonts.googleapis.com/css2?family=Lexend:wght@400;500;600&family=Josefin+Sans:wght@400;600&display=swap">
<style>
:root{
  --teal:#0e3d48;
  --teal-deep:#0a3139;
  --coral:#f4735a;
  --amber:#eeaa3a;
  --peach:#f8b8a2;
  --ink:#2c3a3f;
  --muted:#4a5559;
  --white:#ffffff;
}
*{box-sizing:border-box;margin:0;padding:0}
html,body{width:1200px;height:4758px;overflow:hidden}
body{position:relative;background:var(--white);font-family:"Josefin Sans",sans-serif;color:var(--ink)}
.abs{position:absolute}
h2,h3,.nav,.btn,.label{font-family:"Lexend",sans-serif}
.btn{display:inline-block;background:var(--coral);color:var(--white);border-radius:22px;font-size:13px;text-transform:uppercase;letter-spacing:.3px;text-align:center;line-height:40px;height:40px;text-decoration:none}

/* top bar */
.topbar{left:0;top:0;width:1200px;height:32px;background:var(--teal);color:var(--white);font-size:12px;font-family:"Lexend",sans-serif;text-transform:uppercase}
.topbar span b{color:var(--amber);font-weight:400}
.topbar .call{left:135px;top:9px}
.topbar .mail{right:110px;top:9px}

/* header */
.header{left:0;top:32px;width:1200px;height:73px;background:var(--white)}
.brand{left:100px;top:0;width:164px;height:86px;background:var(--white);display:flex;align-items:center;gap:8px;padding-left:16px;font-family:"Lexend",sans-serif;font-weight:500;font-size:20px;color:var(--teal);z-index:3}
.brand i{width:10px;height:10px;background:var(--amber);border-radius:50%}
.nav{left:450px;top:30px;display:flex;gap:32px;font-size:13px;text-transform:uppercase;color:var(--teal)}
.nav .active{color:var(--coral)}
.lang{left:1002px;top:30px;font-family:"Lexend",sans-serif;font-size:14px;color:var(--teal)}
.lang b{color:var(--coral);font-weight:400}

/* hero */
.hero{left:0;top:105px;width:1200px;height:590px}
.hero-panel{left:111px;top:148px;width:384px;height:273px;background:var(--teal);border:2px solid var(--amber);border-radius:18px;padding:34px 30px;color:var(--white)}
.hero-panel h1{font-family:"Lexend",sans-serif;font-weight:500;font-size:23px;line-height:41px;text-transform:uppercase}
.hero-panel h1 em{font-style:normal;color:var(--amber)}
.hero-panel p{font-size:14px;line-height:34px;margin-top:8px}
.hero-panel .btn{margin-top:14px;width:140px;height:38px;line-height:38px;font-size:12px}

/* section titles */
.title{width:1200px;left:0;text-align:center;font-family:"Lexend",sans-serif;font-weight:500;font-size:26px;color:var(--teal);text-transform:uppercase}
.title::after{content:"";display:block;width:58px;height:4px;margin:10px auto 0;border-top:2px dotted var(--coral)}

/* about */
.about-text{left:633px;top:775px;width:450px}
.about-text h2{font-weight:500;font-size:26px;color:var(--teal);text-transform:uppercase}
.about-text h2::after{content:"";display:block;width:58px;margin-top:6px;border-top:2px dotted var(--coral)}
.about-text p{font-size:15px;line-height:34px;color:var(--muted);margin-top:22px}
.about-text p+p{margin-top:10px}
.about-text .btn{margin-top:26px;width:140px}

/* process */
.process-bg{left:0;top:1272px;width:1200px;height:976px;background:linear-gradient(180deg,#fff 0%,#fde1d6 30%,var(--peach) 100%)}
.step{width:454px;height:255px;background:var(--white);border-radius:28px;box-shadow:0 4px 14px rgba(14,61,72,.08)}
.step.dark{background:var(--teal);color:var(--white)}
.step svg{position:absolute;left:26px;top:50px}
.step .copy{position:absolute;left:250px;top:44px;width:180px}
.step .label{color:var(--coral);font-size:13px;text-transform:uppercase;line-height:30px}
.step p{font-size:15px;line-height:34px;margin-top:8px}
.step .more{color:var(--coral);font-family:"Lexend",sans-serif;font-size:13px;text-decoration:underline;display:block;margin-top:8px}
.step .num{position:absolute;right:30px;bottom:10px;font-family:"Lexend",sans-serif;font-weight:600;font-size:78px;color:rgba(14,61,72,.06);line-height:1}
.step.dark .num{color:rgba(255,255,255,.08)}

/* why */
.reason{width:340px;text-align:center;font-size:15px;line-height:34px;color:var(--muted)}
.reason .ico{width:92px;height:80px;margin:0 auto 14px;border-radius:50%;display:flex;align-items:center;justify-content:center}

/* camps */
.camps-label{font-family:"Lexend",sans-serif;font-weight:500;font-size:21px;color:var(--white);text-transform:uppercase;text-align:center;width:452px}

/* faq */
.faq{left:199px;width:800px;height:44px;border:1.5px solid #8a9ca1;border-radius:8px;font-family:"Lexend",sans-serif;font-size:13px;text-transform:uppercase;color:var(--teal);line-height:41px;padding-left:20px}
.faq::after{content:"";position:absolute;right:22px;top:18px;border:4px solid transparent;border-top:5px solid var(--teal)}

/* footer */
.footer-col h4{font-family:"Lexend",sans-serif;font-weight:500;font-size:16px;color:var(--coral);text-transform:uppercase;margin-bottom:14px}
.footer-col li{list-style:none;font-family:"Lexend",sans-serif;font-size:13px;color:var(--white);text-transform:uppercase;line-height:37px;display:flex;align-items:center;gap:14px}
.footer-col svg{flex:none}
</style>
</head>
<body>

<div class="abs topbar">
  <span class="abs call"><b>CALL US :</b> +41 79 000 12 34</span>
  <span class="abs mail"><b>✉&nbsp; MAIL US :</b> INFO@TINY-THREADDAYS.CH</span>
</div>

<header class="abs header">
  <div class="abs brand"><span>Tiny-ThreadDays</span><i></i></div>
  <nav class="abs nav"><span class="active">Home</span><span>About us</span><span>Process</span><span>Why choose us</span><span>FAQ</span></nav>
  <div class="abs lang"><b>EN</b> / DE / IT</div>
</header>

<section class="abs hero">
  <svg width="1200" height="590" viewBox="0 0 1200 590" class="abs" style="left:0;top:0">
    <defs>
      <linearGradient id="heroFill" x1="0" y1="0" x2="1" y2="1">
        <stop offset="0" stop-color="#7fa7c4"/><stop offset=".45" stop-color="#c9b29a"/><stop offset="1" stop-color="#8a6e4f"/>
      </linearGradient>
    </defs>
    <path d="M0 0H1200V470C1000 610 760 590 600 560C400 525 200 470 0 430Z" fill="var(--coral)"/>
    <path role="img" aria-label="Photo: kids sewing with an instructor at a sunny workshop table with mountain views" d="M0 0H1200V458C1000 596 760 576 600 546C400 512 200 456 0 418Z" fill="url(#heroFill)"/>
  </svg>
  <div class="abs hero-panel">
    <h1>Creative <em>sewing camps</em><br>for kids</h1>
    <p>Small groups · Multilingual instructors · Premium fabrics &amp; Stitchwell machines</p>
    <span class="btn">Book a camp</span>
  </div>
</section>

<!-- about -->
<svg class="abs" style="left:105px;top:775px" width="460" height="375" viewBox="0 0 460 375">
  <circle cx="240" cy="30" r="30" fill="var(--amber)"/>
  <circle cx="425" cy="290" r="12" fill="var(--amber)"/>
  <path d="M40 110C90 60 180 80 230 90C300 100 380 60 425 110C470 170 420 260 360 300C290 350 190 360 110 340C30 320 -10 260 10 190C20 150 20 130 40 110Z" fill="var(--amber)"/>
  <path role="img" aria-label="Photo: instructor helping children at sewing machines, with a premium holiday camps badge" d="M52 118C98 76 180 96 228 104C296 116 372 76 410 120C450 172 406 252 350 288C284 332 190 342 116 322C44 302 14 250 30 190C38 158 36 136 52 118Z" fill="#c7a48a"/>
</svg>
<div class="abs about-text">
  <h2>About us</h2>
  <p>Lena and Mara have over 10 years of experience in teaching children sewing, tailoring, and design with fun, style, and structure.</p>
  <p>In small groups (max. 8 children), we guide young talents through a creative week of vacation – with real results: self-sewn pieces, new friends, and lots of pride.</p>
  <span class="btn">Learn more</span>
</div>

<!-- process -->
<div class="abs process-bg"></div>
<h2 class="abs title" style="top:1214px">How the camp works</h2>

<div class="abs step" style="left:124px;top:1315px">
  <svg width="200" height="160" viewBox="0 0 200 160"><circle cx="114" cy="14" r="13" fill="#8b5a3c"/><circle cx="160" cy="140" r="5" fill="#6b4a6a"/><path role="img" aria-label="Photo: child choosing a model from a sketchbook" d="M20 40C50 10 120 20 160 45C205 75 190 140 140 148C90 156 20 150 8 110C0 80 5 55 20 40Z" fill="#b08a74"/></svg>
  <div class="copy"><div class="label">Project selection</div><p>Your child chooses their own model based on previously produced clothing items</p></div>
  <div class="num">01</div>
</div>

<div class="abs step dark" style="left:620px;top:1315px">
  <svg width="200" height="160" viewBox="0 0 200 160"><circle cx="114" cy="14" r="13" fill="#8b5a3c"/><circle cx="160" cy="140" r="5" fill="#222"/><path role="img" aria-label="Photo: shelves of stacked fabric rolls" d="M20 40C50 10 120 20 160 45C205 75 190 140 140 148C90 156 20 150 8 110C0 80 5 55 20 40Z" fill="#6f7f8c"/></svg>
  <div class="copy"><div class="label">Fabric selection</div><p>High-quality fabrics are available.</p><span class="more">Learn more ↗</span></div>
  <div class="num">02</div>
</div>

<div class="abs step" style="left:124px;top:1612px">
  <svg width="200" height="160" viewBox="0 0 200 160"><circle cx="114" cy="14" r="13" fill="#3d3e46"/><circle cx="160" cy="140" r="5" fill="#555"/><path role="img" aria-label="Photo: child learning to use a sewing machine" d="M20 40C50 10 120 20 160 45C205 75 190 140 140 148C90 156 20 150 8 110C0 80 5 55 20 40Z" fill="#7b7a64"/></svg>
  <div class="copy"><div class="label">Sewing machine operation</div><p>Learn how to use a sewing machine</p></div>
  <div class="num">03</div>
</div>

<div class="abs step" style="left:620px;top:1612px">
  <svg width="200" height="160" viewBox="0 0 200 160"><circle cx="114" cy="14" r="13" fill="#3d3e46"/><circle cx="160" cy="140" r="5" fill="#222"/><path role="img" aria-label="Photo: instructor guiding a child cutting fabric" d="M20 40C50 10 120 20 160 45C205 75 190 140 140 148C90 156 20 150 8 110C0 80 5 55 20 40Z" fill="#8e7865"/></svg>
  <div class="copy"><div class="label">Sewing &amp; refining</div><p>Step by step to the goal with professional guidance</p></div>
  <div class="num">04</div>
</div>

<div class="abs step" style="left:373px;top:1913px">
  <svg width="200" height="160" viewBox="0 0 200 160"><circle cx="114" cy="14" r="13" fill="#4a3f6b"/><circle cx="160" cy="140" r="5" fill="#222"/><path role="img" aria-label="Photo: fashion show on a runway" d="M20 40C50 10 120 20 160 45C205 75 190 140 140 148C90 156 20 150 8 110C0 80 5 55 20 40Z" fill="#5e5a66"/></svg>
  <div class="copy"><div class="label">Showtime!</div><p>Fashion show or photo shoot at the end of the week</p></div>
  <div class="num">05</div>
</div>

<!-- why -->
<h2 class="abs title" style="top:2323px">Why parents choose us</h2>

<div class="abs reason" style="left:79px;top:2425px"><div class="ico" style="background:#e6eeee"><svg width="44" height="44" viewBox="0 0 44 44" fill="none" stroke="var(--teal)" stroke-width="2"><circle cx="22" cy="22" r="18"/><circle cx="22" cy="18" r="5"/><path d="M13 32c2-6 16-6 18 0"/></svg></div>Small groups &amp; personalized attention</div>
<div class="abs reason" style="left:447px;top:2425px"><div class="ico" style="background:#fde6df"><svg width="44" height="44" viewBox="0 0 44 44" fill="none" stroke="var(--coral)" stroke-width="2"><rect x="6" y="8" width="18" height="16" rx="2"/><rect x="20" y="20" width="18" height="16" rx="2"/><path d="M11 14h8M15 12v8M25 32l4-9 4 9"/></svg></div>Multilingual supervision (DE / EN / IT)</div>
<div class="abs reason" style="left:796px;top:2425px"><div class="ico" style="background:#fdf0dc"><svg width="48" height="44" viewBox="0 0 48 44" fill="none" stroke="var(--amber)" stroke-width="2"><path d="M6 18l18-8 18 8-18 8z"/><path d="M6 18v8l18 8 18-8v-8"/></svg></div>High-quality fabrics &amp; top-quality sewing machines (Stitchwell)</div>

<div class="abs reason" style="left:79px;top:2630px"><div class="ico" style="background:#e6eeee"><svg width="44" height="44" viewBox="0 0 44 44" fill="none" stroke="var(--teal)" stroke-width="2"><path d="M22 6a11 11 0 0 0-7 19v5h14v-5A11 11 0 0 0 22 6z"/><path d="M17 35h10M19 39h6M22 14v10"/></svg></div>Encouragement of creativity,<br>self-confidence, and fine motor skills</div>
<div class="abs reason" style="left:447px;top:2630px"><div class="ico" style="background:#fde6df"><svg width="44" height="44" viewBox="0 0 44 44" fill="none" stroke="var(--coral)" stroke-width="2"><path d="M22 6l12 5v9c0 8-6 13-12 16-6-3-12-8-12-16v-9z"/><path d="M17 21l4 4 7-7"/></svg></div>Safe, loving environment in Zurich,<br>various places easy to reach</div>
<div class="abs reason" style="left:796px;top:2630px"><div class="ico" style="background:#fdf0dc"><svg width="44" height="44" viewBox="0 0 44 44" fill="none" stroke="var(--amber)" stroke-width="2"><circle cx="22" cy="22" r="17"/><circle cx="22" cy="18" r="5"/><path d="M13 32c2-6 16-6 18 0"/></svg></div>Pick-up Service from the<br>Main-Station</div>

<!-- upcoming camps -->
<svg class="abs" style="left:0;top:2865px" width="1200" height="590" viewBox="0 0 1200 590"><path d="M0 20C300 -5 600 25 900 8C1020 2 1120 0 1200 10V575C1100 565 1000 585 900 575C600 548 300 580 0 565Z" fill="var(--teal)"/></svg>
<h2 class="abs title" style="top:2932px;color:var(--white)">Upcoming camp</h2>
<div class="abs" role="img" aria-label="Photo: children playing with a colourful parachute on a meadow" style="left:122px;top:3041px;width:452px;height:267px;border-radius:22px;background:linear-gradient(180deg,#c9d8e0 0%,#9bbf7a 55%,#5f8f3a 100%)"></div>
<div class="abs camps-label" style="left:122px;top:3336px">Spring camps</div>
<div class="abs camps-label" style="left:626px;top:3034px">Summer camps</div>
<div class="abs" role="img" aria-label="Photo: kids snorkelling in clear turquoise water" style="left:626px;top:3089px;width:454px;height:268px;border-radius:22px;background:linear-gradient(160deg,#5fc3d0 0%,#2aa1b3 50%,#16778a 100%)"></div>

<!-- faq -->
<h2 class="abs title" style="top:3503px">Frequently asked questions</h2>
<div class="abs faq" style="top:3598px">Does my child need any prior knowledge?</div>
<div class="abs faq" style="top:3679px">How does the pick-up service work?</div>
<div class="abs faq" style="top:3761px">How many items of clothing are produced?</div>
<div class="abs faq" style="top:3842px">What safety measures are in place?</div>
<div class="abs faq" style="top:3923px">Can siblings or friends join the same camp?</div>
<span class="abs btn" style="left:491px;top:4014px;width:218px">View more questions</span>

<!-- footer -->
<svg class="abs" style="left:0;top:4110px" width="1200" height="648" viewBox="0 0 1200 648">
  <path d="M0 40C200 20 380 60 520 110C600 140 700 140 800 100C950 40 1100 30 1200 50V648H0Z" fill="var(--teal)"/>
  <path d="M600 120C750 40 950 20 1200 50V170C1000 160 800 150 600 120Z" fill="#e8eef0"/>
</svg>
<div class="abs" style="left:144px;top:4080px;width:184px;height:184px;border-radius:50%;background:var(--white);display:flex;align-items:center;justify-content:center;font-family:'Lexend',sans-serif;font-weight:500;font-size:17px;color:var(--teal)">Tiny-ThreadDays</div>
<h2 class="abs" style="left:109px;top:4333px;font-weight:500;font-size:25px;color:var(--white);text-transform:uppercase">Ready to book a creative week?</h2>
<span class="abs btn" style="left:940px;top:4329px;width:150px">Book a camp</span>

<div class="abs footer-col" style="left:111px;top:4448px"><h4>Quick links</h4><ul><li>Home</li><li>About us</li><li>Process</li><li>Why choose us</li><li>FAQ</li></ul></div>
<div class="abs footer-col" style="left:339px;top:4448px"><h4>Follow us</h4><ul><li>Lookbook</li><li>Circlepage</li><li>Reelhub</li></ul></div>
<div class="abs footer-col" style="left:552px;top:4448px"><h4>Contact</h4><ul>
  <li><svg width="14" height="14" viewBox="0 0 24 24" fill="var(--coral)"><path d="M6.6 10.8a15 15 0 0 0 6.6 6.6l2.2-2.2a1 1 0 0 1 1-.25 11 11 0 0 0 3.6.6 1 1 0 0 1 1 1V20a1 1 0 0 1-1 1A17 17 0 0 1 3 4a1 1 0 0 1 1-1h3.5a1 1 0 0 1 1 1 11 11 0 0 0 .6 3.6 1 1 0 0 1-.25 1z"/></svg>+41 79 000 56 78</li>
  <li><svg width="14" height="14" viewBox="0 0 24 24" fill="var(--coral)"><path d="M2 5h20v14H2z"/><path d="M2 5l10 8 10-8" stroke="var(--teal)" stroke-width="2" fill="none"/></svg>hello@tiny-threaddays.ch</li>
  <li><svg width="14" height="16" viewBox="0 0 24 28" fill="var(--coral)"><path d="M12 0a10 10 0 0 0-10 10c0 8 10 18 10 18s10-10 10-18A10 10 0 0 0 12 0zm0 14a4 4 0 1 1 0-8 4 4 0 0 1 0 8z"/></svg>Zürich, Switzerland</li></ul></div>
<div class="abs footer-col" style="left:879px;top:4448px"><h4>Sign up</h4>
  <div style="width:208px;height:36px;border:1px solid #4f7580;border-radius:18px;color:var(--white);font-family:'Lexend',sans-serif;font-size:11px;line-height:34px;padding-left:16px">EMAIL ADDRESS</div>
  <span class="btn" style="margin-top:18px;width:92px;height:32px;line-height:32px;font-size:10px">Sign up</span>
</div>

<div class="abs" style="left:0;top:4715px;width:1200px;text-align:center;font-family:'Lexend',sans-serif;font-size:12px;color:var(--white)">© 2025 TINY-THREADDAYS. ALL RIGHTS RESERVED.</div>

</body>
</html>
```